Professional & attention grabbing.

A business card design, front and back. I already have a logo I will attach, but I am open to something new as well.
Things to include:
Name:
Title:
Phone:
Email:
Wanting something that is professional but attention grabbing.
Also we do a lot of work using drones on natural gas pipelines (leading the future)if you want to include any of that. I'm open to ideas.
Target Market(s)
Natural gas transmission industry / greenhouse gas mitigation industry
Industry/Entity Type
Business
Colors
Designer to choose colors to be used in the design.
Look and feel
Each slider illustrates characteristics of the customer's brand and the style your logo design should communicate.

```html
<!DOCTYPE html>
<html lang="en">
<head>
<meta charset="utf-8">
<title>KV Field Inspections — Business Card</title>
<link rel="stylesheet" href="https://fonts.googleapis.com/css2?family=Poppins:wght@400;500;600;700&display=swap">
<style>
  :root {
    --backdrop: #2b2b2d;
    --card-dark: #3a3a3d;
    --card-light: #ffffff;
    --ink-dark: #3a3a3d;
    --ink-light: #ffffff;
    --accent-red: #d0161f;
    --map-tone: #47474a;
  }
  * { margin: 0; padding: 0; box-sizing: border-box; }
  html, body {
    width: 1200px; height: 1000px; overflow: hidden;
    background: var(--backdrop);
    font-family: "Poppins", sans-serif;
  }
  .canvas {
    position: relative; width: 1200px; height: 1000px;
  }
  .card {
    position: absolute; left: 250px; width: 700px; height: 400px;
    overflow: hidden;
    box-shadow: 0 14px 30px rgba(0,0,0,0.45);
  }
  /* Front */
  .card-front { top: 70px; background: var(--card-dark); }
  .world-map-area {
    position: absolute; left: 70px; top: 40px; width: 600px; height: 320px;
    background: radial-gradient(ellipse at 50% 50%, var(--map-tone) 0%, rgba(71,71,74,0.35) 60%, rgba(58,58,61,0) 80%);
    border-radius: 40px;
  }
  .brand {
    position: absolute; display: flex; align-items: center; gap: 16px;
    font-weight: 700; letter-spacing: 0.5px; white-space: nowrap;
  }
  .brand-mark { display: block; }
  .card-front .brand {
    left: 50%; top: 50%; transform: translate(-50%, -50%);
    color: var(--ink-light); font-size: 40px;
  }
  .card-front .brand-mark { width: 34px; height: 34px; background: var(--ink-light); }
  /* Back */
  .card-back { top: 530px; background: var(--card-light); }
  .logo-panel {
    position: absolute; left: 0; top: 0; width: 385px; height: 400px;
    background: var(--card-light);
  }
  .card-back .brand {
    left: 40px; top: 150px; color: var(--ink-dark); font-size: 28px; gap: 12px;
  }
  .card-back .brand-mark { width: 24px; height: 24px; background: var(--accent-red); }
  .info-panel {
    position: absolute; left: 385px; top: 0; width: 315px; height: 400px;
    background: var(--card-dark);
  }
  .panel-pointer {
    position: absolute; left: -12px; top: 224px; width: 0; height: 0;
    border-top: 12px solid transparent; border-bottom: 12px solid transparent;
    border-right: 12px solid var(--card-dark);
  }
  .person { position: absolute; left: 34px; top: 218px; }
  .person-name {
    color: var(--accent-red); font-weight: 700; font-size: 24px;
    letter-spacing: 1px; line-height: 1.1; text-transform: uppercase;
  }
  .person-title {
    color: var(--ink-light); font-weight: 500; font-size: 15px;
    letter-spacing: 0.5px; text-transform: uppercase;
  }
  .contact-list { position: absolute; left: 34px; top: 300px; list-style: none; }
  .contact-item {
    display: flex; align-items: center; gap: 12px;
    color: var(--ink-light); font-size: 15px; line-height: 24px;
  }
  .contact-icon { width: 13px; height: 13px; fill: var(--accent-red); flex: none; }
</style>
</head>
<body>
<main class="canvas">
  <section class="card card-front" aria-label="Card front">
    <div class="world-map-area" role="img" aria-label="Faint dotted world map"></div>
    <div class="brand"><span class="brand-mark"></span>KV Field Inspections</div>
  </section>

  <section class="card card-back" aria-label="Card back">
    <div class="logo-panel">
      <div class="brand"><span class="brand-mark"></span>KV Field Inspections</div>
    </div>
    <div class="info-panel">
      <span class="panel-pointer"></span>
      <div class="person">
        <p class="person-name">Alex Morrow</p>
        <p class="person-title">Founder</p>
      </div>
      <ul class="contact-list">
        <li class="contact-item">
          <svg class="contact-icon" viewBox="0 0 16 16" aria-hidden="true"><path d="M3 1l3 3-1.5 2a9 9 0 0 0 5.5 5.5L12 10l3 3-2 2C7 15 1 9 1 3z"/></svg>
          000 000 0000
        </li>
        <li class="contact-item">
          <svg class="contact-icon" viewBox="0 0 16 16" aria-hidden="true"><path d="M1 3h14v10H1z M1 3l7 6 7-6" fill="none" stroke="#d0161f" stroke-width="1.6"/></svg>
          info@yourmail.com
        </li>
      </ul>
    </div>
  </section>
</main>
</body>
</html>
```